Website Design Project for Beauty & Wellness Professionals

As background information, I have a website that is focused on Beauty & Wellness Professionals:
- Job Search (www.lumarinovo.com)
- Business Classifieds (negocios.lumarinovo.com)
- Freelancer Classifieds (freelancer.lumarinovo.com)
- Course Reviews (cursos.lumarinovo.com)

All those websites use standard templates.

I need a DESIGN for the HOME PAGE (no coding) of the Website Platform that consolidates the four platforms under the same design.

Website designs that we like:
- quelvox.com
- brintmoor.com

Target Market(s)

Brazilian Professionals from Beauty & Wellness sector

Industry/Entity Type

Business

Requirements
Must have
• Website designs that we like:
- quelvox.com
- brintmoor.com

```html
<!DOCTYPE html>
<html lang="en">
<head>
<meta charset="utf-8">
<title>Lumarinovo – Careers in Beauty</title>
<link rel="stylesheet" href="https://fonts.googleapis.com/css2?family=Source+Sans+3:ital,wght@0,400;0,600;0,700;1,400&display=swap">
<style>
:root{
  --sky:#5fbcd9;
  --sky-dark:#3f8fb3;
  --teal:#3a9cc4;
  --ink:#2e2e2e;
  --muted:#8a8a8a;
  --line:#dcdcdc;
  --panel:#f1f1f1;
  --orange:#e8731f;
  --green:#3f9a2a;
  --footer-top:#4ea6c8;
  --footer-bottom:#2f7fa3;
  --footer-bar:#2a7396;
}
*{box-sizing:border-box;margin:0;padding:0}
html,body{width:1200px;height:2590px;overflow:hidden}
body{position:relative;background:#fff;font-family:"Source Sans 3",Arial,sans-serif;color:var(--ink)}
.abs{position:absolute}
a{color:inherit;text-decoration:none}

/* top bar */
.top-bar{top:0;left:0;width:1200px;height:31px;background:var(--sky);display:flex;justify-content:flex-end;align-items:center;padding-right:100px;gap:14px;color:#fff;font-size:13px;font-weight:600}
.top-bar .sep{opacity:.7}

/* header */
.site-header{top:31px;left:0;width:1200px;height:116px;background:#fff;display:flex;align-items:center;padding:0 100px 0 95px}
.brand{display:flex;align-items:center;gap:12px;color:var(--teal);font-size:34px;font-weight:400;width:272px}
.brand-dot{width:42px;height:42px;border-radius:50%;background:var(--teal);opacity:.85}
.social-chips{display:flex;gap:6px;margin-right:18px}
.social-chips span{width:26px;height:26px;background:#b8c3ca;border-radius:3px}
.main-nav{display:flex;font-size:18px;color:#444;margin-left:auto}
.main-nav a{padding:0 14px;border-left:1px solid #ccc}
.main-nav a:first-child{border-left:none}

/* hero */
.hero{top:147px;left:0;width:1200px;height:449px;overflow:hidden}
.hero-photo{position:absolute;inset:0;background:linear-gradient(100deg,#f3f3f1 0%,#e9cdbb 22%,#eac7b1 45%,#efd7c4 60%,#8fd3df 78%,#5fc2d6 100%)}
.hero-copy{position:absolute;left:176px;top:158px;color:#fff;text-shadow:0 2px 6px rgba(0,0,0,.35)}
.hero-copy .kicker{font-size:33px;font-weight:700}
.hero-copy h1{font-size:56px;font-weight:700;line-height:1.05}
.search-bar{position:absolute;left:176px;top:276px;width:850px;height:73px;background:rgba(50,50,50,.78);display:flex;align-items:center;gap:8px;padding:0 14px}
.search-bar .field{height:40px;background:#fff;border:1px solid #ccc;color:#999;font-size:15px;display:flex;align-items:center;padding:0 14px}
.search-bar .select{width:140px;justify-content:space-between;color:#444;background:#eee}
.search-bar .keyword{width:310px}
.search-bar .location{width:220px}
.search-bar .btn{width:136px;height:40px;background:#3aa3cf;color:#fff;font-size:16px;font-weight:600;display:flex;align-items:center;justify-content:center}

/* jobs */
.job-tabs{top:635px;left:307px;display:flex;gap:8px}
.job-tabs span{height:45px;padding:0 16px;display:flex;align-items:center;font-size:16px;background:#ececec;border:1px solid var(--line);border-bottom:none;color:#444}
.job-tabs span.active{background:#fff}
.tabs-rule{top:680px;left:276px;width:648px;height:1px;background:var(--line)}
.job-list{top:690px;left:276px;width:648px;list-style:none}
.job{height:121px;display:flex;padding-top:14px;border-bottom:1px solid var(--line)}
.job-thumb{width:78px;height:78px;border:1px solid var(--line);padding:4px;margin-right:22px}
.job-thumb div{width:100%;height:100%;background:linear-gradient(135deg,#d9b8a0,#6b4a3a)}
.job-info{width:300px}
.job-title{color:var(--teal);font-size:16px;line-height:1.3}
.job-meta{color:var(--muted);font-size:12px;line-height:1.4;margin-top:4px}
.job-place{width:140px;font-size:16px;color:#333;line-height:1.3}
.job-place small{display:block;color:var(--muted);font-size:12px;line-height:1.5}
.job-date{font-size:16px;color:#333}
.job-date small{display:block;color:var(--muted);font-size:12px}
.pager{top:1070px;left:383px;width:450px;height:44px;background:#ececec;display:flex;align-items:center;justify-content:center;gap:8px}
.pager span{height:26px;min-width:26px;padding:0 8px;background:#fff;border:1px solid #ccc;font-size:13px;display:flex;align-items:center;justify-content:center}
.pager .wide{padding:0 14px}

/* section titles */
.section-title{font-size:24px;font-weight:400;color:var(--ink)}
.rule{left:130px;width:912px;height:1px;background:var(--line)}

/* courses */
.courses-title{top:1150px;left:207px}
.course{top:1191px;width:228px}
.course-img{width:228px;height:152px}
.course p{font-size:14px;color:var(--muted);line-height:1.5;margin-top:10px}
.btn-more{display:inline-flex;margin-top:12px;height:36px;width:115px;align-items:center;justify-content:center;background:linear-gradient(#f08a36,#d9621a);color:#fff;font-size:13px;border-radius:2px}

/* testimonials */
.testi-title{top:1517px;left:0;width:1200px;text-align:center}
.testimonial{top:1578px;width:320px}
.testimonial .quote-mark{position:absolute;left:0;top:-4px;font-size:40px;color:#ccc;font-weight:700;line-height:1}
.testimonial .avatar{position:absolute;left:26px;top:0;width:80px;height:74px;background:linear-gradient(135deg,#e0c6b4,#8c6a55)}
.testimonial .lead{margin-left:118px;font-size:12.5px;font-style:italic;color:#444;line-height:1.55}
.testimonial .body{font-size:12.5px;font-style:italic;color:#444;line-height:1.55;margin-top:6px}
.testimonial .author{font-size:12.5px;font-weight:700;margin-top:12px;margin-left:4px}

/* partners */
.partners-title{top:1822px;left:0;width:1200px;text-align:center}
.partner-row{top:1872px;left:158px;width:890px;display:flex;justify-content:space-between;align-items:center}
.partner-badge{width:66px;height:34px;background:#d7dde2;border-radius:4px}
.partner-badge.round{width:44px;height:44px;border-radius:50%}

/* info panels */
.panel{top:2017px;height:148px;background:var(--panel);padding:16px 24px}
.panel h3{font-size:19px;font-weight:400;margin-bottom:12px}
.panel.subscribe h3{color:var(--green)}
.panel.vacancy h3{color:var(--orange)}
.panel.online h3{color:var(--teal)}
.email-field{width:225px;height:28px;background:#fff;border:1px solid #ddd;font-size:12px;color:#999;display:flex;align-items:center;padding:0 8px}
.btn-subscribe{margin:8px 0 0 124px;width:100px;height:30px;background:linear-gradient(#52b03a,#2f8a20);color:#fff;font-size:15px;display:flex;align-items:center;justify-content:center;border-radius:2px}
.vacancy-list{display:grid;grid-template-columns:128px 1fr;row-gap:6px;font-size:12.5px;color:#444;list-style:none}
.vacancy-list li::before{content:"› "}
.panel.online p{font-size:12.5px;color:var(--muted);line-height:1.6}
.panel.online .tag{position:absolute;right:16px;bottom:12px;font-size:11px;color:#666}

/* footer */
.site-footer{top:2219px;left:0;width:1200px;height:305px;background:linear-gradient(var(--footer-top),var(--footer-bottom));border-top:6px solid #a7d3e4;color:#fff}
.site-footer h4{position:absolute;font-size:21px;font-weight:400}
.feed-box{position:absolute;left:123px;top:75px;width:305px;height:192px;background:#fff;padding:14px}
.feed-grid{display:grid;grid-template-columns:repeat(4,62px);gap:8px 10px}
.feed-grid div{height:64px;background:linear-gradient(135deg,#e7cdb9,#9c7560)}
.feed-box small{display:block;color:#aaa;font-size:10px;margin-top:8px}
.tweet-box{position:absolute;left:509px;top:90px;width:273px;height:130px;background:rgba(255,255,255,.18);border-radius:12px;padding:18px 22px;font-size:12.5px;line-height:1.6}
.tweet-box strong{display:block;margin-top:12px;font-weight:600}
.follow-list{position:absolute;left:834px;top:102px;list-style:none}
.follow-list li{display:flex;align-items:center;gap:18px;height:47.5px;font-size:12.5px}
.follow-list .chip{width:36px;height:36px;background:rgba(255,255,255,.3);border-radius:3px}
.footer-bar{top:2524px;left:0;width:1200px;height:66px;background:var(--footer-bar);color:#e3f1f7;font-size:13px;display:flex;align-items:center;justify-content:center;gap:8px}
</style>
</head>
<body>

<div class="abs top-bar"><span>Advertise Job Vacancy</span><span class="sep">|</span><span>Sign In</span><span class="sep">|</span><span>Register</span></div>

<header class="abs site-header">
  <div class="brand"><span class="brand-dot"></span><span>Lumarinovo</span></div>
  <div class="social-chips"><span></span><span></span><span></span><span></span><span></span></div>
  <nav class="main-nav"><a>Blog</a><a>For Business</a><a>Events &amp; Partners</a><a>About Us</a><a>Contact</a></nav>
</header>

<section class="abs hero">
  <div class="hero-photo" role="img" aria-label="Photo of a relaxed woman receiving a facial massage at a spa, with white flowers"></div>
  <div class="hero-copy">
    <div class="kicker">Looking for a Career In Beauty..</div>
    <h1>Find Your Dream Job</h1>
  </div>
  <form class="search-bar">
    <div class="field select">Jobs <svg width="12" height="8" viewBox="0 0 12 8"><path d="M0 0h12L6 8z" fill="#555"/></svg></div>
    <div class="field keyword">Key tittle or company</div>
    <div class="field location">Locations</div>
    <div class="btn">SEARCH</div>
  </form>
</section>

<div class="abs job-tabs"><span class="active">Featured Job Vacancies</span><span>Latest Job Vacancies</span><span>Job Vacancies</span></div>
<div class="abs tabs-rule"></div>
<ul class="abs job-list">
  <li class="job">
    <div class="job-thumb"><div role="img" aria-label="Portrait of the poster"></div></div>
    <div class="job-info"><div class="job-title">Aux. Hairdresser (Escovista) - Santo André (SP)</div><div class="job-meta">Marina Tavel / Orquil Hair and Esthetics - Posted by Marina Tavel</div></div>
    <div class="job-place">Santo André<small>São Paulo, the Federative Republic of Brazil</small></div>
    <div class="job-date">July 18<small>2013</small></div>
  </li>
  <li class="job">
    <div class="job-thumb"><div role="img" aria-label="Portrait of the poster"></div></div>
    <div class="job-info"><div class="job-title">Manicure - Closest subway Vila Madalena - São Paulo (SP)</div><div class="job-meta">RM Manicure and Waxing - Posted by jobs</div></div>
    <div class="job-place">Santo André<small>São Paulo, the Federative Republic of Brazil</small></div>
    <div class="job-date">July 18<small>2013</small></div>
  </li>
  <li class="job">
    <div class="job-thumb"><div role="img" aria-label="Portrait of the poster"></div></div>
    <div class="job-info"><div class="job-title">Manicure - Jabalpur - São Paulo (SP)</div><div class="job-meta">Esmalteria Florenza - Unit Jabalpur - Posted by nobre_carla</div></div>
    <div class="job-place">Santo André<small>São Paulo, the Federative Republic of Brazil</small></div>
    <div class="job-date">July 18<small>2013</small></div>
  </li>
</ul>
<div class="abs pager"><span class="wide">Prev</span><span>1</span><span>2</span><span>3</span><span>4</span><span>5</span><span>6</span><span>...</span><span>22</span><span class="wide">Next</span></div>

<h2 class="abs section-title courses-title">Online Course Vestra</h2>
<article class="abs course" style="left:207px">
  <div class="course-img" role="img" aria-label="Group of women with face masks and colourful headbands" style="background:linear-gradient(135deg,#e07a3a,#8fbf5a)"></div>
  <p>Mauris vel lacus vitae felis vestibulum volutpat. Etiam est nunc venenatis</p>
  <a class="btn-more">READ MORE</a>
</article>
<article class="abs course" style="left:478px">
  <div class="course-img" role="img" aria-label="Woman receiving a relaxing facial treatment" style="background:linear-gradient(135deg,#f2eee6,#9cc07a)"></div>
  <p>Mauris vel lacus vitae felis vestibulum volutpat. Etiam est nunc venenatis</p>
  <a class="btn-more">READ MORE</a>
</article>
<article class="abs course" style="left:749px">
  <div class="course-img" role="img" aria-label="Woman with a clay face mask and a pink flower" style="background:linear-gradient(135deg,#b8c7cf,#e9a0b8)"></div>
  <p>Mauris vel lacus vitae felis vestibulum volutpat. Etiam est nunc venenatis</p>
  <a class="btn-more">READ MORE</a>
</article>

<div class="abs rule" style="top:1488px"></div>

<h2 class="abs section-title testi-title">Customer Testimonials</h2>
<article class="abs testimonial" style="left:104px">
  <span class="quote-mark">“</span><div class="avatar" role="img" aria-label="Customer portrait"></div>
  <p class="lead">Nunc tempus felis vitae urna. Vivamus porttitor, neque at volutpat rutrum, purus nisi eleifend libero, a tempus libero lectus</p>
  <p class="body">Morbi eget arcu. Morbi porta, libero id ullamcorper non-ummy, nibh ligula pulvinar metus, eget consectetuer augue nisi quis lacus. Ut ac mi quis lacus. ”</p>
  <p class="author">By Author Name</p>
</article>
<article class="abs testimonial" style="left:445px">
  <span class="quote-mark">“</span><div class="avatar" role="img" aria-label="Customer portrait"></div>
  <p class="lead">Nunc tempus felis vitae urna. Vivamus porttitor, neque at volutpat rutrum, purus nisi eleifend libero, a tempus libero lectus</p>
  <p class="body">Morbi eget arcu. Morbi porta, libero id ullamcorper non-ummy, nibh ligula pulvinar metus, eget consectetuer augue nisi quis lacus. Ut ac mi quis lacus. ”</p>
  <p class="author">By Author Name</p>
</article>
<article class="abs testimonial" style="left:782px">
  <span class="quote-mark">“</span><div class="avatar" role="img" aria-label="Customer portrait"></div>
  <p class="lead">Nunc tempus felis vitae urna. Vivamus porttitor, neque at volutpat rutrum, purus nisi eleifend libero, a tempus libero lectus</p>
  <p class="body">Morbi eget arcu. Morbi porta, libero id ullamcorper non-ummy, nibh ligula pulvinar metus, eget consectetuer augue nisi quis lacus. Ut ac mi quis lacus. ”</p>
  <p class="author">By Author Name</p>
</article>

<div class="abs rule" style="top:1796px"></div>

<h2 class="abs section-title partners-title">Our Companies &amp; Partners</h2>
<div class="abs partner-row">
  <span class="partner-badge"></span><span class="partner-badge"></span><span class="partner-badge"></span><span class="partner-badge"></span><span class="partner-badge"></span><span class="partner-badge round"></span><span class="partner-badge"></span><span class="partner-badge"></span><span class="partner-badge round"></span>
</div>

<div class="abs rule" style="top:1968px"></div>

<section class="abs panel subscribe" style="left:166px;width:269px">
  <h3>Assinar Por Email</h3>
  <div class="email-field">email address</div>
  <div class="btn-subscribe">Subscribe</div>
</section>
<section class="abs panel vacancy" style="left:458px;width:272px">
  <h3>Job Vacancy</h3>
  <ul class="vacancy-list"><li>Assistant Hairdresser</li><li>Designer Eyebrow</li><li>Assistant Cleaning</li><li>Featured</li><li>Hairdresser</li><li>Nurse</li></ul>
</section>
<section class="abs panel online" style="left:755px;width:269px">
  <h3>Online Courses Vestra</h3>
  <p>Nunc tempus felis vitae urna. Vivamus porttitor, g, purus nisi eleifend libero, a tempus libero lectus feugiat felis.</p>
  <span class="tag">vestra</span>
</section>

<footer class="abs site-footer">
  <h4 style="left:123px;top:32px">Friendwall Feed</h4>
  <div class="feed-box">
    <div class="feed-grid">
      <div role="img" aria-label="Member photo"></div><div role="img" aria-label="Member photo"></div><div role="img" aria-label="Member photo"></div><div role="img" aria-label="Member photo"></div>
      <div role="img" aria-label="Member photo"></div><div role="img" aria-label="Member photo"></div><div role="img" aria-label="Member photo"></div><div role="img" aria-label="Member photo"></div>
    </div>
    <small>friendwall page</small>
  </div>
  <h4 style="left:515px;top:32px">Chirpline Updates</h4>
  <div class="tweet-box">@ Suspendisse quam leo, molestie sed luctus quis, feugiat in, pede.<strong>Check it out : https://docs.velamora.com/</strong></div>
  <h4 style="left:834px;top:32px">Follow Us</h4>
  <ul class="follow-list">
    <li><span class="chip"></span>On Chirpline</li>
    <li><span class="chip"></span>As RSS Feed</li>
    <li><span class="chip"></span>Shared on Friendwall</li>
    <li><span class="chip"></span>On Circlenet</li>
  </ul>
</footer>
<div class="abs footer-bar"><span>© 2013 www.lumarinovo.com</span>|<span>Term and Conditions</span>|<span>Privacy Statement</span>|<span>Imprint</span>|<span>Glassary</span></div>

</body>
</html>
```